New tech executive consulting company needs professionally branded document templates

We are a new business selling fractional board advisory and go-to-market consulting services into the Technology space. Tessaly Brink are experts in providing high-quality executive-level leaders on a part-time basis to tech companies in need of their expertise. We work closely with clients to understand their business needs, challenges, and goals, and provides customised solutions to help them succeed. Due to our audience we need the design to have a high quality, executive look and feel.

Our first website is live and can be found at tessalybrink.example. We also already have a logo which I've uploaded. Our brand is clean and uses orange to give it colour and an identity that stands out.

We need some document master templates created so we can create our own presentations (Google Slides & Powerpoint), PDF documents, and Word templates, and ideally also a LinkedIn banner.

```html
<!DOCTYPE html>
<html lang="en">
<head>
<meta charset="utf-8">
<title>Tessaly Brink — Presentation Templates</title>
<link href="https://fonts.googleapis.com/css2?family=Poppins:wght@500;600;700&family=Roboto:wght@400;500;700&display=swap" rel="stylesheet">
<style>
:root{
  --orange:#e8804a;
  --navy:#1f2a37;
  --text:#3a3f47;
  --muted:#6b7079;
  --paper:#ffffff;
  --canvas:#e6e5e8;
}
*{margin:0;padding:0;box-sizing:border-box}
html,body{width:1200px;height:4021px;overflow:hidden;background:var(--canvas)}
body{position:relative;font-family:"Roboto",Arial,sans-serif;color:var(--text)}
.slide{position:absolute;left:81px;width:1038px;height:584px;background:var(--paper);overflow:hidden;box-shadow:0 2px 10px rgba(0,0,0,.06)}
.abs{position:absolute}
.decor{position:absolute;inset:0;width:100%;height:100%}
.photo{position:absolute;inset:0;width:100%;height:100%}
.brand{position:absolute;font-family:"Poppins",Arial,sans-serif;font-weight:600;font-size:30px;line-height:36px;letter-spacing:3px;color:var(--navy);text-align:right}
.heading{font-family:"Poppins",Arial,sans-serif;font-weight:700;color:var(--navy);text-transform:uppercase}
.body-copy{font-size:14.5px;line-height:26px;text-align:justify;color:var(--text)}
.body-copy p+p{margin-top:10px}
.contact{display:flex;align-items:center;gap:14px;font-family:"Roboto",Arial,sans-serif;font-weight:500;color:var(--navy)}
.icon{width:38px;height:38px;flex:none}
.card{position:absolute;background:var(--paper);box-shadow:0 6px 30px rgba(0,0,0,.10)}
.step{position:absolute;width:300px;text-align:center}
.step-photo{width:203px;height:203px;border-radius:50%;margin:0 auto;border:3px solid #fff;box-shadow:0 4px 14px rgba(0,0,0,.15)}
.step h3{margin-top:30px;font-size:15px;font-weight:700;color:var(--navy)}
.step p{margin-top:12px;font-size:14.5px;line-height:26px;color:var(--muted)}
</style>
</head>
<body>

<!-- Slide 1: Welcome -->
<section class="slide" style="top:81px">
  <svg class="decor" viewBox="0 0 1038 584">
    <defs>
      <linearGradient id="g1" x1="0" y1="0" x2="1" y2="1">
        <stop offset="0" stop-color="#b9b3aa"/><stop offset=".5" stop-color="#4a5872"/><stop offset="1" stop-color="#c9b8a0"/>
      </linearGradient>
    </defs>
    <polygon points="0,0 690,0 280,584 0,584" fill="url(#g1)" role="img" aria-label="Photo of two colleagues reviewing a tablet in an office"/>
    <polygon points="674,0 700,0 290,584 264,584" fill="var(--orange)"/>
    <polygon points="300,330 318,330 492,584 474,584" fill="var(--orange)"/>
  </svg>
  <div class="brand" style="right:62px;top:40px">TESSALY<br>BRINK</div>
  <div class="abs heading" style="left:559px;top:263px;font-size:22px;font-weight:600">Welcome to</div>
  <div class="abs heading" style="left:557px;top:296px;font-size:46px;line-height:54px">Tessaly Brink</div>
  <div class="abs" style="left:559px;top:360px;width:420px;font-family:Poppins,Arial,sans-serif;font-size:20px;line-height:29px;color:var(--navy)">Experts in providing executive leadership on demand</div>
  <div class="abs contact" style="left:557px;top:430px;font-size:18px;color:var(--orange)">
    <svg class="icon" viewBox="0 0 38 38"><circle cx="19" cy="19" r="17.5" fill="none" stroke="var(--orange)" stroke-width="1.5"/><path d="M13 11l4 1 1 4-2 1.5c1 2.5 3 4.5 5.5 5.5l1.5-2 4 1 1 4c-1 1.5-2.5 2-4 2-7 -1-12-6-13-13 0-1.5.5-3 2-4z" fill="none" stroke="var(--orange)" stroke-width="1.5" stroke-linejoin="round"/></svg>
    <span>+44 7700 900418</span>
  </div>
</section>

<!-- Slide 2: About -->
<section class="slide" style="top:737px">
  <svg class="decor" viewBox="0 0 1038 584">
    <defs>
      <linearGradient id="g2" x1="0" y1="0" x2="1" y2="1">
        <stop offset="0" stop-color="#5d6f66"/><stop offset=".5" stop-color="#a7b2ae"/><stop offset="1" stop-color="#3d4450"/>
      </linearGradient>
    </defs>
    <polygon points="574,0 1038,0 1038,584 504,584" fill="url(#g2)" role="img" aria-label="Photo of a smiling woman leading a meeting in a bright office"/>
    <polygon points="560,0 570,0 500,584 490,584" fill="var(--orange)"/>
  </svg>
  <div class="brand" style="left:59px;top:20px;text-align:left">TESSALY<br>BRINK</div>
  <div class="abs heading" style="left:59px;top:117px;font-size:25px;color:var(--orange)">About</div>
  <div class="abs heading" style="left:59px;top:150px;font-size:29px;line-height:39px;font-weight:600">The smart way to<br>scale your business</div>
  <div class="abs body-copy" style="left:59px;top:236px;width:390px">
    <p>Tessaly Brink are experts in providing high-quality executive-level leaders on a part-time basis to tech companies in need of their expertise. We work closely with clients to understand their business needs, challenges, and goals, and provides customised solutions to help them succeed.</p>
    <p>Our strategic insights, leadership, and collaborative approach make us a valuable partner for companies looking to drive growth and innovation. We are passionate about helping companies achieve their goals and are committed to providing the highest level of service to our clients.</p>
  </div>
</section>

<!-- Slide 3: Profile -->
<section class="slide" style="top:1390px">
  <div class="brand" style="left:59px;top:18px;text-align:left">TESSALY<br>BRINK</div>
  <svg class="decor" viewBox="0 0 1038 584">
    <polygon points="820,123 865,123 841,164 796,164" fill="var(--orange)"/>
    <polygon points="564,506 609,506 585,545 540,545" fill="var(--orange)"/>
  </svg>
  <div class="card" style="left:59px;top:164px;width:919px;height:342px"></div>
  <div class="abs" style="left:54px;top:208px;width:4px;height:250px;background:var(--orange)"></div>
  <div class="abs heading" style="left:106px;top:196px;font-size:30px;font-weight:600">Rowan Castell</div>
  <div class="abs body-copy" style="left:106px;top:246px;width:487px">
    <p>Rowan Castell is a highly accomplished business leader with extensive experience in executive-level leadership and strategy. As the founder of Tessaly Brink, Rowan brings his years of experience in the technology industry to help companies achieve their goals.</p>
    <p>Throughout his career, Rowan has held executive positions in companies ranging from startups to large corporations. He has a deep understanding of the tech industry and has helped companies at all stages of maturity drive significant growth and innovation.</p>
  </div>
  <svg class="abs" style="left:623px;top:180px" width="310" height="310" viewBox="0 0 310 310">
    <defs>
      <linearGradient id="g3" x1="0" y1="0" x2="0" y2="1">
        <stop offset="0" stop-color="#7f9a8e"/><stop offset=".55" stop-color="#c9a58b"/><stop offset="1" stop-color="#2f4a6e"/>
      </linearGradient>
    </defs>
    <rect x="58" y="58" width="194" height="194" rx="26" transform="rotate(45 155 155)" fill="url(#g3)" stroke="var(--orange)" stroke-width="3" role="img" aria-label="Portrait photo of the founder"/>
  </svg>
</section>

<!-- Slide 4: Statement -->
<section class="slide" style="top:2046px">
  <div class="brand" style="right:62px;top:16px">TESSALY<br>BRINK</div>
  <div class="abs" style="left:53px;top:84px;width:454px;height:468px;border:2px solid var(--orange)"></div>
  <svg class="abs" style="left:62px;top:75px" width="451" height="465" viewBox="0 0 451 465">
    <defs>
      <linearGradient id="g4" x1="0" y1="0" x2="1" y2="1">
        <stop offset="0" stop-color="#8a6a52"/><stop offset=".5" stop-color="#d9d6d2"/><stop offset="1" stop-color="#3e3b3a"/>
      </linearGradient>
    </defs>
    <rect width="451" height="465" fill="url(#g4)" role="img" aria-label="Photo of a smiling businesswoman in a meeting with a laptop"/>
  </svg>
  <svg class="decor" viewBox="0 0 1038 584">
    <polygon points="830,139 874,139 848,186 804,186" fill="var(--orange)"/>
    <polygon points="584,510 626,510 604,548 562,548" fill="var(--orange)"/>
  </svg>
  <div class="card" style="left:395px;top:186px;width:583px;height:324px"></div>
  <div class="abs heading" style="left:462px;top:270px;font-size:37px;line-height:51px;font-weight:600">Experts in providing<br>executive leadership<br>on demand</div>
</section>

<!-- Slide 5: How it works -->
<section class="slide" style="top:2700px">
  <div class="brand" style="right:62px;top:17px">TESSALY<br>BRINK</div>
  <div class="abs heading" style="left:0;width:1038px;top:86px;text-align:center;font-size:30px;font-weight:600">How it works</div>
  <div class="step" style="left:54px;top:162px">
    <div class="step-photo" role="img" aria-label="Photo of a team working together at a laptop" style="background:linear-gradient(135deg,#c98a5c,#e7e3df 50%,#3f5a80)"></div>
    <h3>Lorem ipsum dolor sit amet</h3>
    <p>Lorem ipsum dolor consectetur adipiscing elit, sed do eiusmod tempor incididunt cupidatat magna aliqua.</p>
  </div>
  <div class="step" style="left:373px;top:162px">
    <div class="step-photo" role="img" aria-label="Photo of colleagues reviewing work at a computer" style="background:linear-gradient(135deg,#b7c6cf,#4d5a6a 55%,#1f2a37)"></div>
    <h3>Lorem ipsum dolor sit amet</h3>
    <p>Lorem ipsum dolor consectetur adipiscing elit, sed do eiusmod tempor incididunt cupidatat magna aliqua.</p>
  </div>
  <div class="step" style="left:691px;top:162px">
    <div class="step-photo" role="img" aria-label="Photo of two professionals discussing at a desk" style="background:linear-gradient(135deg,#d7d4cf,#5b6f8a 55%,#2b3646)"></div>
    <h3>Lorem ipsum dolor sit amet</h3>
    <p>Lorem ipsum dolor consectetur adipiscing elit, sed do eiusmod tempor incididunt cupidatat magna aliqua.</p>
  </div>
</section>

<!-- Slide 6: Thank you -->
<section class="slide" style="top:3355px">
  <svg class="decor" viewBox="0 0 1038 584">
    <defs>
      <linearGradient id="g6" x1="0" y1="0" x2="1" y2="1">
        <stop offset="0" stop-color="#d8d2c8"/><stop offset=".5" stop-color="#a8835f"/><stop offset="1" stop-color="#eeeae4"/>
      </linearGradient>
    </defs>
    <polygon points="400,0 1038,0 1038,584 792,584" fill="url(#g6)" role="img" aria-label="Photo of two businesswomen looking at a laptop together"/>
    <polygon points="375,0 400,0 792,584 767,584" fill="var(--orange)"/>
    <polygon points="878,320 894,320 598,584 582,584" fill="var(--orange)"/>
  </svg>
  <div class="brand" style="left:64px;top:28px;text-align:left">TESSALY<br>BRINK</div>
  <div class="abs heading" style="left:59px;top:245px;font-size:70px;line-height:84px;letter-spacing:1px">Thank you</div>
  <div class="abs contact" style="left:61px;top:355px;font-size:18px">
    <svg class="icon" viewBox="0 0 38 38"><circle cx="19" cy="19" r="17.5" fill="none" stroke="var(--orange)" stroke-width="1.5"/><path d="M13 11l4 1 1 4-2 1.5c1 2.5 3 4.5 5.5 5.5l1.5-2 4 1 1 4c-1 1.5-2.5 2-4 2-7 -1-12-6-13-13 0-1.5.5-3 2-4z" fill="none" stroke="var(--orange)" stroke-width="1.5" stroke-linejoin="round"/></svg>
    <span>+44 7700 900418</span>
  </div>
  <div class="abs contact" style="left:61px;top:418px;font-size:18px">
    <svg class="icon" viewBox="0 0 38 38"><circle cx="19" cy="19" r="17.5" fill="none" stroke="var(--orange)" stroke-width="1.5"/><rect x="11" y="13" width="16" height="12" rx="1.5" fill="none" stroke="var(--orange)" stroke-width="1.5"/><path d="M11.5 14l7.5 6 7.5-6" fill="none" stroke="var(--orange)" stroke-width="1.5"/></svg>
    <span>info@tessalybrink.example</span>
  </div>
  <div class="abs contact" style="left:61px;top:479px;font-size:18px">
    <svg class="icon" viewBox="0 0 38 38"><circle cx="19" cy="19" r="17.5" fill="none" stroke="var(--orange)" stroke-width="1.5"/><circle cx="19" cy="15" r="4" fill="none" stroke="var(--orange)" stroke-width="1.5"/><path d="M11.5 27c1-4 4-6 7.5-6s6.5 2 7.5 6" fill="none" stroke="var(--orange)" stroke-width="1.5"/></svg>
    <span>Rowan Castell</span>
  </div>
</section>

</body>
</html>
```